Shine Fox Auto Care Business Card

2 side business card design for an auto detailing business

Target Market(s)

Auto detailing

Contact Information for Business Card

Things included

The business name “Shine Fox Auto Care”
Mark Dunrow
(403)271-6094
Corvell Bay, Sk

Services offered - complete interior& exterior detail
- paint correction & protection
- ceramic coating
- trim restore
- auto carpet & seat cleaning

Requirements
Must have
• Colours that are in my logo

Services offered

My name Mark Dunrow
403-271-6094
Corvell Bay, Sk

Not too sure in what order for these ?
Website. Shinefoxautocare.com
Instagram Shinefoxautocare
Email. Shinefoxautoac@mailvento.com

```html
<!DOCTYPE html>
<html lang="en">
<head>
<meta charset="utf-8">
<title>Shine Fox Auto Care – Business Card</title>
<link href="https://fonts.googleapis.com/css2?family=Open+Sans:ital,wght@0,400;0,600;0,800;1,400&display=swap" rel="stylesheet">
<style>
  :root {
    --bg: #2a2a2c;
    --card-white: #ffffff;
    --card-black: #141415;
    --brand-red: #9b1b1f;
    --ink: #222224;
    --muted: #5a5a5e;
    --light: #e9e9ea;
  }
  * { margin: 0; padding: 0; box-sizing: border-box; }
  html, body { width: 1200px; height: 900px; overflow: hidden; }
  body {
    background: var(--bg);
    font-family: "Open Sans", sans-serif;
    display: flex; flex-direction: column; align-items: center; justify-content: center;
    gap: 32px;
  }
  .card {
    position: relative; width: 700px; height: 400px; overflow: hidden;
    box-shadow: 0 10px 30px rgba(0,0,0,.45);
  }
  .card--front { background: var(--card-white); }
  .card--back { background: var(--card-black); }

  .swoosh { position: absolute; inset: 0; }

  .brand {
    position: absolute; left: 70px; top: 95px;
    display: flex; align-items: center; gap: 16px;
  }
  .brand__dot {
    width: 62px; height: 62px; border-radius: 50%;
    background: var(--brand-red);
  }
  .brand__name {
    font-weight: 800; font-size: 30px; line-height: 1.05;
    color: var(--ink); text-transform: uppercase; letter-spacing: .5px;
  }

  .website {
    position: absolute; left: 40px; top: 300px;
    color: var(--light); font-size: 17px;
    transform: rotate(12deg); transform-origin: left center;
  }

  .divider {
    position: absolute; left: 395px; top: 120px;
    width: 2px; height: 185px; background: var(--brand-red);
  }

  .contact { position: absolute; left: 420px; top: 118px; }
  .contact__name {
    color: var(--brand-red); font-weight: 800; font-size: 27px;
    text-transform: uppercase; line-height: 1.1;
  }
  .contact__title { color: var(--muted); font-size: 19px; margin-bottom: 10px; }
  .contact__list { list-style: none; }
  .contact__item {
    display: flex; align-items: center; gap: 8px;
    color: var(--muted); font-size: 16px; line-height: 1.55;
  }
  .icon { width: 14px; height: 14px; flex: none; fill: var(--brand-red); }

  .back__circle {
    position: absolute; right: 90px; top: 60px;
    width: 130px; height: 130px; border-radius: 50%;
    background: #1d1d1f;
  }
  .services {
    position: absolute; left: 55px; top: 255px;
    color: var(--light); font-size: 19px; line-height: 1.6;
  }
  .services__dot { color: var(--brand-red); padding: 0 6px; }
</style>
</head>
<body>

  <section class="card card--front">
    <svg class="swoosh" viewBox="0 0 700 400" aria-hidden="true">
      <path d="M0,226 C170,236 250,282 370,345 C450,384 570,378 700,318 L700,400 L0,400 Z" fill="#9b1b1f"/>
      <path d="M0,240 C170,252 245,298 365,360 C445,398 570,394 700,336 L700,400 L0,400 Z" fill="#ffffff"/>
      <path d="M0,245 C170,258 242,305 360,366 C440,404 570,400 700,342 L700,400 L0,400 Z" fill="#141415"/>
    </svg>

    <div class="brand">
      <span class="brand__dot"></span>
      <span class="brand__name">Shine Fox<br>Auto Care</span>
    </div>

    <p class="website">Shinefoxautocare.com</p>

    <span class="divider"></span>

    <div class="contact">
      <h1 class="contact__name">Mark Dunrow</h1>
      <p class="contact__title">President</p>
      <ul class="contact__list">
        <li class="contact__item">
          <svg class="icon" viewBox="0 0 24 24"><path d="M6.6 10.8a15.1 15.1 0 0 0 6.6 6.6l2.2-2.2a1 1 0 0 1 1-.25 11.4 11.4 0 0 0 3.6.57 1 1 0 0 1 1 1V20a1 1 0 0 1-1 1A17 17 0 0 1 3 4a1 1 0 0 1 1-1h3.5a1 1 0 0 1 1 1c0 1.250.2 2.45.57 3.57a1 1 0 0 1-.25 1z"/></svg>
          403-271-6094
        </li>
        <li class="contact__item">
          <svg class="icon" viewBox="0 0 24 24"><path d="M2 5h20v14H2z M2 5l10 8 10-8" fill="none" stroke="#9b1b1f" stroke-width="2"/></svg>
          Shinefoxautoac@mailvento.com
        </li>
        <li class="contact__item">
          <svg class="icon" viewBox="0 0 24 24"><circle cx="12" cy="12" r="9" fill="none" stroke="#9b1b1f" stroke-width="2.5"/></svg>
          Shinefoxautocare
        </li>
        <li class="contact__item">
          <svg class="icon" viewBox="0 0 24 24"><path d="M12 2a7 7 0 0 0-7 7c0 5 7 13 7 13s7-8 7-13a7 7 0 0 0-7-7zm0 9.5A2.5 2.5 0 1 1 12 6.5a2.5 2.5 0 0 1 0 5z"/></svg>
          Corvell Bay, Sk
        </li>
      </ul>
    </div>
  </section>

  <section class="card card--back">
    <span class="back__circle"></span>
    <p class="services">
      complete interior&amp; exterior detail<span class="services__dot">•</span>paint correction &amp; protection<br>
      ceramic coating<span class="services__dot">•</span>trim restore<span class="services__dot">•</span>auto carpet &amp; seat cleaning
    </p>
  </section>

</body>
</html>
```